Business Card Design Project

We're looking for a unique business card design that stands out from the rest, using the brand and logo we've already developed.
Two-sided design please.
Quillmark Media (www.quillmarkmedia.com.au) is a digitally-focused advertising agency that has produces results-driven campaigns. As a result, we'd like our business card to reflect our innovative approach.
Size, shape, orientation, etc, are all flexible (providing the print costs don't become ridiculous or we have to sit there with tiny scissors!).
Business card should include space for name, title, email, mobile, landline and address.
Industry/Entity Type
Advertising
Look and feel

```html
<!DOCTYPE html>
<html lang="en">
<head>
<meta charset="utf-8">
<title>Quillmark Media — Business Card</title>
<link rel="stylesheet" href="https://fonts.googleapis.com/css2?family=Open+Sans:wght@400;600&display=swap">
<style>
  :root {
    --brand-red: #ed1c24;
    --card-white: #ffffff;
    --ink: #1a1a1a;
    --backdrop: #e9e6e2;
  }
  * { margin: 0; padding: 0; box-sizing: border-box; }
  html, body {
    width: 1200px;
    height: 1200px;
    overflow: hidden;
    background: var(--backdrop);
    font-family: "Open Sans", Arial, sans-serif;
  }
  .canvas {
    position: relative;
    width: 1200px;
    height: 1200px;
  }
  .card {
    position: absolute;
    left: 150px;
    width: 900px;
    height: 520px;
    border-radius: 22px;
    overflow: hidden;
    box-shadow: 0 6px 18px rgba(0,0,0,0.18);
  }
  .card-front { top: 50px; }
  .card-back { top: 630px; }
  .card-art {
    position: absolute;
    inset: 0;
    width: 900px;
    height: 520px;
  }
  .wordmark {
    position: absolute;
    color: var(--ink);
    font-weight: 600;
    white-space: nowrap;
    letter-spacing: 0.01em;
  }
  .card-front .wordmark {
    left: 100px;
    top: 208px;
    font-size: 76px;
    line-height: 1;
  }
  .card-back .wordmark {
    left: 0;
    width: 900px;
    text-align: center;
    top: 125px;
    font-size: 50px;
    line-height: 1;
  }
  .contact-fields {
    position: absolute;
    top: 262px;
    list-style: none;
    color: var(--card-white);
    font-size: 32px;
    line-height: 40px;
    font-weight: 400;
  }
  .contact-fields.personal { left: 70px; }
  .contact-fields.reach { left: 475px; }
</style>
</head>
<body>
<main class="canvas">

  <section class="card card-front" aria-label="Card front">
    <svg class="card-art" viewBox="0 0 900 520" aria-hidden="true">
      <rect width="900" height="520" fill="var(--brand-red)"/>
      <rect y="100" width="900" height="320" fill="var(--card-white)"/>
      <ellipse cx="400" cy="260" rx="345" ry="218" fill="var(--card-white)"/>
    </svg>
    <div class="wordmark">Quillmark Media</div>
  </section>

  <section class="card card-back" aria-label="Card back">
    <svg class="card-art" viewBox="0 0 900 520" aria-hidden="true">
      <rect width="900" height="520" fill="var(--card-white)"/>
      <rect y="105" width="900" height="310" fill="var(--brand-red)"/>
      <ellipse cx="450" cy="260" rx="290" ry="205" fill="var(--brand-red)"/>
    </svg>
    <div class="wordmark">Quillmark Media</div>
    <ul class="contact-fields personal">
      <li>Name:</li>
      <li>Title:</li>
      <li>Email:</li>
    </ul>
    <ul class="contact-fields reach">
      <li>Mobile:</li>
      <li>Landline:</li>
      <li>Address:</li>
    </ul>
  </section>

</main>
</body>
</html>
```